BOLD & MINIMALIST DESIGN NEEDED

We want a very bold but minimalistic business card design that is impactful and utilizes both sides of the business card. Our current logo is included for your use.

We want bold fonts and good use of negative space. We don't want the logo to overpower the design.

Target Market(s)

Professionals who are building new commercial buildings.

Industry/Entity Type

Construction

Contact Information for Business Card

Name, Title, email, office phone, cell phone, website

Font styles to use
Serif
Sans Serif

Requirements
Must have
• Bold design!

```html
<!DOCTYPE html>
<html lang="en">
<head>
<meta charset="utf-8">
<title>Ridgeline Design + Build — Business Card</title>
<link rel="stylesheet" href="https://fonts.googleapis.com/css2?family=Lato:wght@400;700;900&display=swap">
<style>
  :root {
    --canvas-bg: #e6e4e0;
    --card-black: #0d0d0d;
    --card-white: #f7f7f7;
    --ink: #0a0a0a;
    --paper-text: #ffffff;
    --accent-green: #7cc242;
  }
  * { box-sizing: border-box; margin: 0; padding: 0; }
  html, body {
    width: 1200px;
    height: 900px;
    overflow: hidden;
    background: var(--canvas-bg);
    font-family: "Lato", sans-serif;
  }
  .canvas {
    width: 1200px;
    height: 900px;
    display: flex;
    flex-direction: column;
    align-items: center;
    justify-content: center;
    gap: 36px;
  }
  .card {
    width: 700px;
    height: 400px;
    position: relative;
    overflow: hidden;
    box-shadow: 0 10px 28px rgba(0,0,0,0.22);
  }

  /* Front side */
  .card--front {
    background: var(--card-black);
    display: flex;
    align-items: center;
    justify-content: center;
  }
  .brand {
    display: flex;
    align-items: center;
    gap: 18px;
  }
  .brand__square {
    width: 34px;
    height: 34px;
    background: var(--accent-green);
  }
  .brand__name {
    color: var(--paper-text);
    font-weight: 900;
    font-size: 40px;
    letter-spacing: 0.02em;
    text-transform: uppercase;
    line-height: 1;
  }

  /* Back side */
  .card--back {
    background: var(--card-white);
    color: var(--ink);
    padding: 36px 56px 0 62px;
  }
  .person__name {
    font-weight: 900;
    font-size: 60px;
    line-height: 0.92;
    letter-spacing: -0.01em;
    text-transform: uppercase;
  }
  .person__title {
    margin-top: 6px;
    font-weight: 400;
    font-size: 22px;
    line-height: 1.2;
    letter-spacing: 0.16em;
    text-transform: uppercase;
  }
  .contact {
    position: absolute;
    left: 62px;
    right: 56px;
    top: 194px;
    display: flex;
    justify-content: space-between;
    align-items: flex-start;
  }
  .contact__labels {
    border-left: 8px solid var(--accent-green);
    padding-left: 22px;
    list-style: none;
  }
  .contact__labels li {
    font-weight: 900;
    font-size: 22px;
    letter-spacing: 0.1em;
    line-height: 34px;
    text-transform: uppercase;
  }
  .contact__values {
    list-style: none;
    text-align: right;
    padding-top: 34px;
  }
  .contact__values li {
    font-weight: 400;
    font-size: 22px;
    line-height: 34px;
  }
  .contact__values .phone { letter-spacing: 0.12em; }
</style>
</head>
<body>
  <main class="canvas">
    <section class="card card--front" aria-label="Card front">
      <div class="brand">
        <span class="brand__square" aria-hidden="true"></span>
        <span class="brand__name">Ridgeline Design + Build</span>
      </div>
    </section>

    <section class="card card--back" aria-label="Card back">
      <h1 class="person__name">Martin<br>Calloway</h1>
      <p class="person__title">Principal Designer</p>
      <div class="contact">
        <ul class="contact__labels">
          <li>Office</li>
          <li>Cell</li>
          <li>Email</li>
          <li>Web</li>
        </ul>
        <ul class="contact__values">
          <li class="phone">(555) 240-3187</li>
          <li class="phone">(555) 618-2094</li>
          <li>martin@ridgelinebuild.com</li>
          <li>www.ridgelinebuild.com</li>
        </ul>
      </div>
    </section>
  </main>
</body>
</html>
```